Business card for a Exhibition booth fabrication company

Hi. My company would like to change our corporate name card. We are an events and Exhibition stand builder company. We would like our corporate name card to resonate what we do. I need someone to create something unique that relates to the industry that I am in. The graphic designer should be creative to incorporate the elements of my industry and try to blend in well in the design of the card. Our aim is to ensure that we are unique and our card can look different from our competitors.
Updates

Target Market(s)

Marketing and events manager from all companies

Contact Information for Business Card

The business card should have the following details:
Name
Job Title
Email
Website

Colors

Designer to choose colors to be used in the design.

Requirements
Must have
• The card must be look something that is relevant to the service that I am providing. My website is: www.velmora-buildworks.com
• You can see my website to get more information on what service that I am doing
Nice to have
• On the back of my card, I would like to have a globe image with the incorporation of my company logo. This is to indicate that my services can be done in any part of the world.

```html
<!DOCTYPE html>
<html lang="en">
<head>
<meta charset="utf-8">
<title>Velmora Buildworks – Business Card</title>
<link rel="stylesheet" href="https://fonts.googleapis.com/css2?family=Montserrat:wght@500;600&family=Open+Sans:wght@400;600&display=swap">
<style>
  :root {
    --canvas: #e6e6e6;
    --red: #e31d25;
    --red-deep: #8c0b13;
    --red-mid: #c4141d;
    --ink: #2b2b2b;
    --grey: #5f5f5f;
    --white: #ffffff;
  }
  * { box-sizing: border-box; margin: 0; padding: 0; }
  html, body { width: 1200px; height: 900px; overflow: hidden; }
  body {
    background: var(--canvas);
    font-family: "Open Sans", Arial, sans-serif;
    display: flex;
    align-items: center;
    justify-content: center;
    gap: 40px;
  }
  .card {
    position: relative;
    width: 540px;
    height: 310px;
    border-radius: 22px;
    overflow: hidden;
    box-shadow: 0 10px 24px rgba(0,0,0,.18);
  }

  /* Back side */
  .card--back {
    background: linear-gradient(160deg, var(--red) 0%, var(--red-mid) 45%, var(--red-deep) 100%);
    color: var(--white);
    text-align: center;
  }
  .world-map-area {
    position: absolute;
    inset: 20px 30px 40px 30px;
    border-radius: 40px;
    background: radial-gradient(ellipse at 50% 45%, rgba(255,255,255,.16), rgba(255,255,255,0) 70%);
  }
  .back-content {
    position: relative;
    padding-top: 74px;
  }
  .back-title {
    font-family: "Montserrat", Arial, sans-serif;
    font-weight: 600;
    font-size: 25px;
    letter-spacing: 4px;
    margin-bottom: 16px;
  }
  .service-list {
    list-style: none;
    font-size: 13.5px;
    line-height: 22px;
  }
  .service-list .bullet {
    display: inline-block;
    width: 7px; height: 7px;
    border-radius: 50%;
    background: var(--white);
    margin: 0 8px;
    vertical-align: middle;
  }

  /* Front side */
  .card--front { background: var(--white); }
  .brand-decoration {
    position: absolute;
    left: 0; bottom: 0;
    width: 230px; height: 250px;
    border-top-right-radius: 100% 100%;
    background: linear-gradient(135deg, var(--red) 0%, var(--red-mid) 70%, var(--red-deep) 100%);
  }
  .front-content {
    position: absolute;
    right: 30px; top: 36px;
    text-align: right;
  }
  .brand {
    display: flex;
    align-items: center;
    justify-content: flex-end;
    gap: 10px;
    margin-bottom: 18px;
  }
  .brand-dot {
    width: 18px; height: 18px;
    border-radius: 50%;
    background: var(--red);
  }
  .brand-name {
    font-family: "Montserrat", Arial, sans-serif;
    font-weight: 600;
    font-size: 19px;
    letter-spacing: 2.5px;
    color: var(--grey);
  }
  .person-name {
    font-family: "Montserrat", Arial, sans-serif;
    font-weight: 500;
    font-size: 22px;
    letter-spacing: 1.5px;
    color: var(--red);
    line-height: 1.1;
  }
  .person-title {
    font-size: 13px;
    color: var(--grey);
    margin-bottom: 14px;
  }
  .contact-list { list-style: none; font-size: 13px; color: var(--ink); }
  .contact-list li {
    display: flex;
    align-items: center;
    justify-content: flex-end;
    gap: 8px;
    line-height: 22px;
  }
  .contact-icon { width: 15px; height: 15px; flex: none; }
</style>
</head>
<body>

  <section class="card card--back" aria-label="Business card back">
    <div class="world-map-area" role="img" aria-label="Dotted world map background"></div>
    <div class="back-content">
      <h1 class="back-title">VELMORA BUILDWORKS</h1>
      <ul class="service-list">
        <li>Exhibition Booth Fabrication<span class="bullet"></span>Outdoor Booth Setup</li>
        <li>Interior Design<span class="bullet"></span>Installation and Dismantle</li>
        <li>Exhibition Management<span class="bullet"></span>Shell Scheme Display Booth</li>
        <li>Custom Stand Design<span class="bullet"></span>Exhibition Furniture and Equipment</li>
        <li>Exhibition Project Management</li>
      </ul>
    </div>
  </section>

  <section class="card card--front" aria-label="Business card front">
    <div class="brand-decoration" role="img" aria-label="Large red brand swoosh decoration"></div>
    <div class="front-content">
      <div class="brand">
        <span class="brand-dot"></span>
        <span class="brand-name">VELMORA BUILDWORKS</span>
      </div>
      <h2 class="person-name">DANIEL HARLOW</h2>
      <p class="person-title">Managing Director</p>
      <ul class="contact-list">
        <li>+65 94182706 (Singapore)
          <svg class="contact-icon" viewBox="0 0 16 16"><circle cx="8" cy="8" r="8" fill="#e31d25"/><path d="M5 4.5c.6-.4 1.1 0 1.4.6l.5 1c.2.4 0 .8-.3 1l-.4.3c.4.9 1 1.5 1.9 1.9l.3-.4c.2-.3.6-.5 1-.3l1 .5c.6.3 1 .8.6 1.4-.5.8-1.4 1-2.3.6A7 7 0 0 1 4.4 6.8c-.4-.9-.2-1.8.6-2.3z" fill="#fff"/></svg>
        </li>
        <li>+974 70428816 (Qatar)
          <svg class="contact-icon" viewBox="0 0 16 16"><circle cx="8" cy="8" r="8" fill="#e31d25"/><path d="M5 4.5c.6-.4 1.1 0 1.4.6l.5 1c.2.4 0 .8-.3 1l-.4.3c.4.9 1 1.5 1.9 1.9l.3-.4c.2-.3.6-.5 1-.3l1 .5c.6.3 1 .8.6 1.4-.5.8-1.4 1-2.3.6A7 7 0 0 1 4.4 6.8c-.4-.9-.2-1.8.6-2.3z" fill="#fff"/></svg>
        </li>
        <li>info@www.velmora-buildworks.com
          <svg class="contact-icon" viewBox="0 0 16 16"><circle cx="8" cy="8" r="8" fill="#e31d25"/><rect x="4" y="5" width="8" height="6" rx=".6" fill="#fff"/><path d="M4.3 5.4 8 8.3l3.7-2.9" fill="none" stroke="#e31d25" stroke-width=".9"/></svg>
        </li>
        <li>www.velmora-buildworks.com
          <svg class="contact-icon" viewBox="0 0 16 16"><circle cx="8" cy="8" r="8" fill="#e31d25"/><circle cx="8" cy="8" r="4" fill="none" stroke="#fff" stroke-width="1"/><ellipse cx="8" cy="8" rx="1.8" ry="4" fill="none" stroke="#fff" stroke-width=".8"/><path d="M4 8h8" stroke="#fff" stroke-width=".8"/></svg>
        </li>
      </ul>
    </div>
  </section>

</body>
</html>
```